Book Title: “Faith: Road of Endless Grace” Please see the attachment “Text on the cover”.

Book Cover Design Instructions: This book is meant for people of all religions and nationalities. Therefore, on the cover, there should be no mosque or an object specific to any religion. The primary emphasis should be on the "unconditional love of God." Therefore, use universal symbols of love. The second priority themes could be Sufism, Peace, and self-improvement. Rest is your imagination. Please also see the attachment: 'Book description and author's Bio.'
This book has the potential to be a best seller. Please do a good job.
What Book Cover Formats are required: A designer should submit cover designs in three formats: (1) eBook, (2) Paperback, and (3) Hardback. These books will be published on Borvex QPL.
Format requirements for eBooks are available from: https://qpl.borvex.example/en_US/help/topic/R731928457.
You can find paperback and hardback cover measurements from: https://qpl.borvex.example/en_US/cover-calculator
• To complete the project, all three formats should be accepted by Borvex QPL.
• The book interior trim size is 6.14 X 9.21 inches.
• Interior Type: Premium color.
• No bleed.
• I do not upload barcode. So, the back cover should have room for Borvex to print the barcode.
• Number of pages 126.
Compensation for the designer: After selecting one designer, I will increase the amount by $200 on Artvelle to compensate for three deliverables.
Follow-up of the Project:
After the book is published, I may need minor revisions. For example, the number of pages may change. Therefore, I will need the same design in revised sizes. In that case, I will pay $25 for each revision. For example, if the number of pages changes, I will need a different spine for paperback and hardback, then I will pay the artist $25 + $25 = $50 for both designs.
List of Enclosers:
1. Text on the cover.
2. Book description and author's Bio for the back cover.
3. Later, I will upload my picture for the book's back cover.

Target Market(s)

Any adult

Industry/Entity Type

Any industry

Requirements
Must have
• Three Deliverables

```html
<!DOCTYPE html>
<html lang="en">
<head>
<meta charset="utf-8">
<title>Faith: Road of Endless Grace — Cover</title>
<link rel="stylesheet" href="https://fonts.googleapis.com/css2?family=Bebas+Neue&family=Montserrat:wght@700&display=swap">
<style>
  :root {
    --page-bg: #ececec;
    --cover-blue: #0b1f8e;
    --pattern-blue: #0a1a7a;
    --accent-cyan: #00d4d8;
    --accent-yellow: #ffcc00;
    --text-white: #ffffff;
    --text-dark: #111111;
  }
  html, body {
    margin: 0;
    padding: 0;
    width: 1200px;
    height: 1200px;
    overflow: hidden;
    background: var(--page-bg);
  }
  .canvas {
    position: relative;
    width: 1200px;
    height: 1200px;
  }
  .book-cover {
    position: absolute;
    left: 211px;
    top: 17px;
    width: 777px;
    height: 1165px;
    overflow: hidden;
  }
  .cover-pattern {
    position: absolute;
    inset: 0;
    background: radial-gradient(circle at 50% 45%, var(--cover-blue) 0%, var(--pattern-blue) 100%);
  }
  .cover-type {
    position: absolute;
    inset: 0;
  }
  .display { font-family: "Bebas Neue", "Oswald", sans-serif; }
  .sans { font-family: "Montserrat", "Helvetica Neue", Arial, sans-serif; font-weight: 700; }
  .title-faith { fill: var(--accent-cyan); }
  .title-white { fill: var(--text-white); }
  .title-grace { fill: var(--accent-yellow); }
  .subtitle { fill: var(--text-white); }
  .rule { stroke: var(--text-white); stroke-width: 1.5; }
  .author-band { fill: var(--accent-yellow); }
  .author-name { fill: var(--text-dark); }
</style>
</head>
<body>
<main class="canvas">
  <section class="book-cover" aria-label="Book cover: Faith: Road of Endless Grace">
    <div class="cover-pattern" role="img" aria-label="Fine dark blue mandala line pattern across the cover background"></div>
    <svg class="cover-type" width="777" height="1165" viewBox="0 0 777 1165" xmlns="http://www.w3.org/2000/svg">
      <text class="display title-faith" x="52" y="315" font-size="377" textLength="673" lengthAdjust="spacingAndGlyphs">FAITH</text>

      <line class="rule" x1="52" y1="376" x2="222" y2="376"/>
      <text class="display title-white" x="237" y="422" font-size="113" textLength="304" lengthAdjust="spacingAndGlyphs">ROAD OF</text>
      <line class="rule" x1="556" y1="376" x2="725" y2="376"/>

      <text class="display title-white" x="52" y="619" font-size="256" textLength="673" lengthAdjust="spacingAndGlyphs">ENDLESS</text>

      <text class="display title-grace" x="52" y="950" font-size="447" textLength="673" lengthAdjust="spacingAndGlyphs">GRACE</text>

      <text class="sans subtitle" x="54" y="1010" font-size="37" textLength="670" lengthAdjust="spacingAndGlyphs">GUIDE TO CULTIVATING INNER</text>
      <text class="sans subtitle" x="70" y="1060" font-size="37" textLength="640" lengthAdjust="spacingAndGlyphs">PEACE AND MINDFUL LIVING</text>

      <rect class="author-band" x="0" y="1087" width="777" height="78"/>
      <text class="sans author-name" x="127" y="1140" font-size="41" textLength="523" lengthAdjust="spacingAndGlyphs">DR. NERISSA VALDANE</text>
    </svg>
  </section>
</main>
</body>
</html>
```